Building technology company seek stationery design and folder design

Letterhead, and a folder design
ideally, I would have two letter head design, one is for one-page bussiness letter. the other one I can use for longer document such report, or analysis regular report page
you can find company logo and overall style at our website:
www.structavolt.example

we are in building technology business, using internet of things technology to improve building energy efficiency to make building greener.

Industry/Entity Type

It Company

Requirements
Must have
• company logo
Nice to have
• techy look abstract graphics, etc.
Should not have
• no comment

```html
<!DOCTYPE html>
<html lang="en">
<head>
<meta charset="utf-8">
<title>StructaVolt Stationery</title>
<link href="https://fonts.googleapis.com/css2?family=Questrial&display=swap" rel="stylesheet">
<style>
  :root {
    --bg: #dcdcdc;
    --paper: #ffffff;
    --paper-shade: #ececec;
    --ink: #555a5c;
    --ink-soft: #7a7f81;
    --green: #8cc63f;
    --folder: #1f3236;
    --folder-trace: #2e4549;
    --footer: #0f1d1f;
  }
  * { margin: 0; padding: 0; box-sizing: border-box; }
  html, body { width: 1200px; height: 821px; overflow: hidden; background: var(--bg); }
  body { position: relative; font-family: "Questrial", sans-serif; color: var(--ink); }

  .letterhead {
    position: absolute; left: 74px; top: 114px; width: 441px; height: 620px;
    background: var(--paper); overflow: hidden;
  }
  .letterhead-pattern {
    position: absolute; inset: 0;
    background: linear-gradient(100deg, var(--paper-shade) 0%, var(--paper) 45%, var(--paper-shade) 100%);
  }
  .brand {
    position: absolute; display: flex; align-items: center; gap: 8px;
    color: var(--green); letter-spacing: 0.08em; white-space: nowrap;
  }
  .brand-mark { background: var(--green); }
  .letterhead .brand { left: 50%; top: 80px; transform: translateX(-50%); font-size: 20px; }
  .letterhead .brand-mark { width: 16px; height: 16px; }

  .letter { position: absolute; left: 40px; top: 174px; width: 364px; }
  .salutation { font-size: 11px; margin-bottom: 18px; color: var(--ink); }
  .letter p.body { font-size: 6px; line-height: 9.5px; color: var(--ink-soft); margin-bottom: 9.5px; text-align: justify; }
  .closing { font-size: 6px; color: var(--ink-soft); margin-top: 18px; }
  .signature {
    position: absolute; left: 36px; top: 434px; width: 80px; height: 30px;
    background: linear-gradient(90deg, rgba(140,198,63,0.25), rgba(140,198,63,0.08));
  }
  .letter-footer {
    position: absolute; left: 0; bottom: 0; width: 100%; height: 24px;
    background: var(--footer); border-top: 3px solid var(--green);
    display: flex; align-items: center; justify-content: center;
    font-size: 6px; color: #ffffff; white-space: nowrap; gap: 3px;
  }
  .letter-footer .label { color: var(--green); }

  .folder {
    position: absolute; left: 552px; top: 76px; width: 521px; height: 660px;
    background: var(--folder); overflow: hidden;
  }
  .folder-pattern {
    position: absolute; inset: 0;
    background: radial-gradient(ellipse at 60% 40%, var(--folder-trace) 0%, var(--folder) 70%);
  }
  .folder .brand { left: 50%; top: 330px; transform: translateX(-50%); font-size: 40px; gap: 14px; }
  .folder .brand-mark { width: 30px; height: 30px; }
</style>
</head>
<body>
  <section class="letterhead">
    <div class="letterhead-pattern" role="img" aria-label="Faint grey circuit-trace pattern"></div>
    <div class="brand"><span class="brand-mark"></span><span class="brand-name">STRUCTAVOLT</span></div>
    <div class="letter">
      <p class="salutation">Dear Mr. Harlow,</p>
      <p class="body">Thank you for meeting with our team last week to review the energy performance of your portfolio. Our sensor network can track heating, cooling and lighting loads across each floor in real time, giving your managers clear data to reduce waste and lower monthly operating costs.</p>
      <p class="body">We propose a phased rollout that starts with the two main office towers. Each phase includes installation, calibration and a monthly review of the dashboard so your staff can see savings as they happen and adjust schedules with confidence. Training for facility teams is included at no extra cost.</p>
      <p class="body">Our engineers will also prepare a baseline report covering lighting, ventilation and plug loads. This report sets clear targets for the first year and shows where simple control changes can deliver quick gains. We expect measurable results within the first quarter after the system goes live, with full payback well inside three years.</p>
      <p class="body">Please review the attached proposal and let us know a convenient time to discuss next steps. We look forward to helping your buildings run greener and more efficiently for years to come.</p>
      <p class="closing">Sincerely,</p>
    </div>
    <div class="signature" role="img" aria-label="Handwritten signature of Dana Whitfield"></div>
    <footer class="letter-footer">
      <span class="label">Phone:</span><span>(555) 014-2870</span>
      <span class="label">Email:</span><span>info@structavolt.example</span>
      <span class="label">Web:</span><span>www.structavolt.example</span>
      <span class="label">Social</span><span>: structavolt</span>
    </footer>
  </section>

  <section class="folder">
    <div class="folder-pattern" role="img" aria-label="Subtle dark circuit-trace pattern"></div>
    <div class="brand"><span class="brand-mark"></span><span class="brand-name">STRUCTAVOLT</span></div>
  </section>
</body>
</html>
```